KVOR Individual and Corporate Development Business Card Design

KVOR needs a business card design that is aligned with it's values and targetted markets. Coherent Lattice of Adaptive Reasoning Method's self diagnosis model and tools, which can be used for personal improvement and team/business performance enhancement, is based on the learnings of over 20 years of medical practitioning. KVOR supercharges personal effectiveness and awareness to also increase team and business performance.

The targetted markets are high performance individuals and teams who aspire seek to enhance their capabilities and achieve their absolute best potential.

Look and feel for the business card design we are looking for is high technology, premium, fresh, new and medical.

Target Market(s)

Industry/Entity Type

Business Consultant

Contact Information for Business Card

Logo, Full Name, Title, Phone number, Email, company name, Address,

Font styles to use
Sans Serif

Requirements
Must have
• Tag line: Building Sharper Focus for Truly Capable Minds
• Please use same colours as the logo.

```html
<!DOCTYPE html>
<html lang="en">
<head>
<meta charset="utf-8">
<title>KVOR Business Card</title>
<link rel="stylesheet" href="https://fonts.googleapis.com/css2?family=Ubuntu:wght@400;500;700&display=swap">
<style>
  :root {
    --teal: #17b8c6;
    --teal-deep: #0b97a8;
    --teal-light: #2fcad6;
    --paper: #f4f5f5;
    --grey: #8b8e92;
    --grey-dark: #6f7276;
    --white: #ffffff;
    --stage: #e9ebec;
  }
  * { margin: 0; padding: 0; box-sizing: border-box; }
  html, body { width: 1200px; height: 780px; overflow: hidden; }
  body {
    background: var(--stage);
    font-family: "Ubuntu", sans-serif;
    position: relative;
  }
  .card {
    position: absolute;
    width: 540px;
    height: 320px;
    top: 230px;
    border-radius: 3px;
    overflow: hidden;
    box-shadow: 0 6px 18px rgba(0,0,0,0.14);
  }
  .card--front { left: 40px; background: var(--paper); }
  .card--back {
    left: 620px;
    background: linear-gradient(135deg, var(--teal-light) 0%, var(--teal) 45%, var(--teal-deep) 100%);
  }
  .front-shapes { position: absolute; inset: 0; }
  .brand {
    position: absolute;
    top: 38px;
    left: 250px;
    display: flex;
    align-items: center;
    gap: 12px;
  }
  .brand__square { width: 22px; height: 22px; background: var(--teal); }
  .brand__name {
    font-weight: 700;
    font-size: 46px;
    letter-spacing: 3px;
    color: var(--teal);
    line-height: 1;
  }
  .web {
    position: absolute;
    top: 128px;
    right: 20px;
    font-size: 12px;
    color: var(--white);
    letter-spacing: 0.3px;
  }
  .details {
    position: absolute;
    left: 32px;
    top: 146px;
    width: 300px;
    color: var(--white);
  }
  .person__name { font-size: 15px; font-weight: 500; letter-spacing: 0.8px; text-transform: uppercase; line-height: 18px; }
  .person__title { font-size: 12px; line-height: 14px; margin-top: 1px; }
  .rule { height: 1px; background: rgba(255,255,255,0.75); margin: 7px 0; width: 220px; }
  .address, .contact { font-size: 11.5px; line-height: 15px; }
  .contact li { list-style: none; display: flex; align-items: center; gap: 6px; }
  .contact svg { width: 12px; height: 12px; flex: none; }
  .tagline { font-weight: 500; font-size: 12px; line-height: 16px; }
  .back-name {
    position: absolute;
    left: 60px;
    top: 118px;
    color: var(--white);
    font-weight: 500;
    font-size: 25px;
    line-height: 34px;
    letter-spacing: 1px;
    text-transform: uppercase;
  }
</style>
</head>
<body>
  <section class="card card--front" aria-label="Business card front">
    <svg class="front-shapes" viewBox="0 0 540 320" aria-hidden="true">
      <polygon points="0,120 330,160 540,160 540,320 0,320" fill="var(--teal)"/>
      <polygon points="340,124 540,124 540,158 320,158" fill="var(--grey)"/>
      <polygon points="320,158 540,158 540,162 330,162" fill="var(--grey-dark)"/>
    </svg>
    <div class="brand">
      <span class="brand__square"></span>
      <span class="brand__name">KVOR</span>
    </div>
    <div class="web">www.kvorlattice.com</div>
    <div class="details">
      <p class="person__name">Nora Ellison</p>
      <p class="person__title">Founder</p>
      <div class="rule"></div>
      <p class="address">PO Box 48 Harbour Lane<br>3rd Avenue Kelston</p>
      <ul class="contact">
        <li>
          <svg viewBox="0 0 12 12"><circle cx="6" cy="6" r="5.5" fill="none" stroke="#fff"/><rect x="4" y="3" width="4" height="6" rx="0.8" fill="#fff"/></svg>
          (123) 555-0142
        </li>
        <li>
          <svg viewBox="0 0 12 12"><circle cx="6" cy="6" r="5.5" fill="none" stroke="#fff"/><rect x="3" y="4" width="6" height="4" fill="#fff"/><polyline points="3,4 6,6.3 9,4" fill="none" stroke="#17b8c6" stroke-width="0.8"/></svg>
          hello@kvorlattice.com
        </li>
      </ul>
      <div class="rule"></div>
      <p class="tagline">Building Sharper Focus<br>for Truly Capable Minds</p>
    </div>
  </section>

  <section class="card card--back" aria-label="Business card back">
    <p class="back-name">Coherent Lattice<br>of Adaptive Reasoning Method</p>
  </section>
</body>
</html>
```